Boutique custom software development company needs new business card

Our nearly 20 year old custom software development company would like to better include the fact that we are now providing Bitcoin services. These new services are B2B include education (how to acquire and securely hold Bitcoin) and integrating Bitcoin payments into existing ecommerce sites or other existing systems. Please keep the card clean and simple. Attached is our current design and some other files. vextorial.com

Target Market(s)

businesses owners interested in long term relationship

Industry/Entity Type

Custom software development and Bitcoin

Contact Information for Business Card

Dale Parker, dale@vextorial.com, vextorial.com, (888) 555-VXTRL

Font styles to use
Other font styles liked:
• monospace

Requirements
Must have
• double-sided
Nice to have
• clean and simple
Should not have
• physical address

```html
<!DOCTYPE html>
<html lang="en">
<head>
<meta charset="utf-8">
<title>Vextorial Business Card</title>
<link rel="stylesheet" href="https://fonts.googleapis.com/css2?family=Kanit:wght@600&family=Open+Sans:wght@400;700&display=swap">
<style>
  :root {
    --backdrop: #1e1e1e;
    --card: #ffffff;
    --brand-blue: #3b74be;
    --brand-orange: #f07f22;
    --ink: #1a1a1a;
    --rule: #2a2a2a;
  }
  * { box-sizing: border-box; margin: 0; padding: 0; }
  html, body { width: 1200px; height: 936px; overflow: hidden; }
  body {
    background: var(--backdrop);
    position: relative;
    font-family: "Open Sans", sans-serif;
  }
  .card {
    position: absolute;
    width: 560px;
    height: 320px;
    background: var(--card);
    box-shadow: 0 10px 30px rgba(0,0,0,.5);
  }
  .card--front { left: 80px; top: 100px; }
  .card--back { left: 560px; top: 516px; }

  /* front */
  .front-brand {
    position: absolute;
    left: 0; right: 0; top: 100px;
    text-align: center;
  }
  .brand-wordmark {
    font-family: "Kanit", sans-serif;
    font-weight: 600;
    font-size: 64px;
    line-height: 1;
    letter-spacing: 1px;
    color: var(--brand-blue);
  }
  .brand-tagline {
    margin-top: 8px;
    font-size: 24px;
    color: var(--brand-blue);
    letter-spacing: -.3px;
  }

  /* back */
  .back-brand {
    position: absolute;
    top: 34px; left: 0; right: 0;
    display: flex; align-items: center; justify-content: center; gap: 12px;
  }
  .brand-square {
    width: 30px; height: 30px;
    background: var(--brand-orange);
  }
  .back-brand .brand-wordmark { font-size: 40px; }
  .holder-name {
    position: absolute;
    top: 112px; left: 0; right: 0;
    text-align: center;
    font-family: "Kanit", sans-serif;
    font-weight: 600;
    font-size: 40px;
    line-height: 1;
  }
  .holder-name .first { color: var(--brand-orange); }
  .holder-name .last { color: var(--brand-blue); }
  .contact-rule {
    position: absolute;
    left: 40px; right: 40px;
    height: 1px;
    background: var(--rule);
  }
  .contact-rule--top { top: 186px; }
  .contact-rule--bottom { top: 228px; }
  .contact-row {
    position: absolute;
    top: 194px; left: 40px; right: 40px;
    display: flex; justify-content: space-between; align-items: center;
  }
  .contact-item {
    display: flex; align-items: center; gap: 6px;
    font-size: 14px; color: var(--ink);
  }
  .contact-item svg { width: 16px; height: 16px; flex: none; }
  .services {
    position: absolute;
    top: 244px; left: 0; right: 0;
    text-align: center;
    font-size: 15px;
    color: var(--ink);
  }
  .services .dot { color: var(--brand-orange); padding: 0 6px; }
</style>
</head>
<body>
  <section class="card card--front" aria-label="Card front">
    <div class="front-brand">
      <div class="brand-wordmark">VEXTORIAL</div>
      <div class="brand-tagline">developer of custom applications</div>
    </div>
  </section>

  <section class="card card--back" aria-label="Card back">
    <div class="back-brand">
      <span class="brand-square"></span>
      <span class="brand-wordmark">VEXTORIAL</span>
    </div>
    <h1 class="holder-name"><span class="first">Dale</span> <span class="last">Parker</span></h1>

    <div class="contact-rule contact-rule--top"></div>
    <div class="contact-row">
      <span class="contact-item">
        <svg viewBox="0 0 16 16" aria-hidden="true"><path fill="#f07f22" d="M3.6 1.5l2.3 2.6-1.3 1.8c.9 2 2.5 3.6 4.5 4.5l1.8-1.3 2.6 2.3-1.3 2.4C7 13.6 2.4 9 1.2 2.8z"/></svg>
        (888) 555-VXTRL
      </span>
      <span class="contact-item">
        <svg viewBox="0 0 16 16" aria-hidden="true"><rect x="1" y="3" width="14" height="10" rx="1" fill="#f07f22"/><path d="M1.5 3.8L8 9l6.5-5.2" fill="none" stroke="#fff" stroke-width="1.3"/></svg>
        dale@vextorial.com
      </span>
      <span class="contact-item">
        <svg viewBox="0 0 16 16" aria-hidden="true"><circle cx="8" cy="8" r="7" fill="#f07f22"/><path d="M1 8h14M8 1c-3 3.5-3 10.5 0 14M8 1c3 3.5 3 10.5 0 14" fill="none" stroke="#fff" stroke-width="1"/></svg>
        www.vextorial.com
      </span>
    </div>
    <div class="contact-rule contact-rule--bottom"></div>
    <p class="services">Custom Software<span class="dot">•</span>Bitcoin Education<span class="dot">•</span>Bitcoin Payment Integration</p>
  </section>
</body>
</html>
```